New homepage and Product page - Lumen Vq

Reason: I have narrowed it done to 3 designers and just need to get the designs revised

Industry/Entity Type

Product

```html
<!DOCTYPE html>
<html lang="en">
<head>
<meta charset="utf-8">
<title>Lumen Vq – Home</title>
<link href="https://fonts.googleapis.com/css2?family=Mulish:wght@300;400;600;700&family=Gochi+Hand&display=swap" rel="stylesheet">
<style>
:root{
  --green:#4f8d12;
  --green-bright:#7cc21e;
  --lime:#c9ef5a;
  --olive:#5b6630;
  --text:#666260;
  --text-dark:#5a5552;
  --panel-top:#f5f5f3;
  --panel-bottom:#e6e4e0;
  --footer:#ebe7e2;
  --rule:#cfcac4;
  --badge:#5d554f;
  --gold:#e9a514;
  --social:#9c9a97;
}
*{margin:0;padding:0;box-sizing:border-box}
html,body{width:1200px;height:1000px;overflow:hidden;background:#fff}
body{position:relative;font-family:"Mulish",sans-serif;color:var(--text)}
.abs{position:absolute}

.hero{left:0;top:0;width:1200px;height:250px;background:linear-gradient(180deg,#7cc51f 0%,#62a913 55%,#4c8e0c 100%);overflow:hidden}
.hero-copy{left:119px;top:2px;width:470px;color:#fff;font-weight:700;font-size:16.5px;line-height:23.5px}
.btn-learn{left:120px;top:113px;width:176px;height:50px;background:var(--olive);border:3px solid #fff;border-radius:3px;color:#fff;font-size:18px;font-weight:400;display:flex;align-items:center;padding-left:15px;letter-spacing:.3px}
.btn-learn span{color:var(--lime);font-weight:700;margin-left:12px}
.tagline{left:315px;top:112px;font-family:"Gochi Hand",cursive;font-size:33px;color:var(--lime)}
.beans{left:555px;top:0;width:215px;height:190px;border-radius:0 0 60% 40%;background:radial-gradient(ellipse at 55% 40%,#9cc36a 0%,#7e9f4c 55%,rgba(110,150,50,0) 100%)}
.product-pack{left:770px;top:0;width:282px;height:198px;background:linear-gradient(180deg,#fde35a 0%,#f4f4f2 22%,#e8ebe4 100%);box-shadow:0 4px 8px rgba(0,0,0,.2)}
.hero-notch{left:0;top:226px}

.section-title{left:0;top:300px;width:1200px;text-align:center;font-size:40px;font-weight:300;color:var(--green)}
.section-lead{left:180px;top:352px;width:840px;text-align:center;font-size:20.5px;line-height:30px;color:var(--text)}

.panel{left:120px;top:460px;width:958px;height:270px;border:1px solid #dcdad6;background:linear-gradient(180deg,var(--panel-top),var(--panel-bottom))}
.panel-head{left:120px;top:460px;width:530px;height:40px;background:var(--green);color:#fff;font-size:21px;font-weight:400;padding:7px 0 0 23px;letter-spacing:.3px}
.feature{left:142px;width:485px}
.feature h3{font-size:17.5px;font-weight:600;color:var(--text-dark);margin-left:31px;line-height:24px}
.feature p{font-size:14.8px;line-height:22px;margin:2px 0 0 32px;color:var(--text)}
.feature svg{position:absolute;left:0;top:0}
.photo-person{left:632px;top:430px;width:200px;height:300px;border-radius:90px 90px 0 0;background:linear-gradient(180deg,#4a2f22 0%,#c99a80 40%,#e7c3ae 75%,#d9d6d0 100%)}
.photo-leaves{left:768px;top:445px;width:180px;height:150px;border-radius:50%;background:radial-gradient(ellipse,#8fcf3a 0%,rgba(140,200,60,.5) 55%,rgba(140,200,60,0) 75%)}
.guarantee-seal{left:943px;top:480px}
.guarantee-copy{left:828px;top:601px;width:235px;font-size:15px;line-height:22.5px;color:var(--text)}
.guarantee-copy b{color:var(--text-dark);font-weight:700}

.trust-badge{left:119px;top:767px}
.trust-copy{left:206px;top:772px;width:385px;font-size:13.4px;line-height:20.5px}
.trust-copy a{color:var(--green-bright);font-weight:700;text-decoration:none}
.usa-shield{left:620px;top:772px}
.usa-copy{left:703px;top:769px;width:360px;font-size:14px;line-height:21px}
.usa-copy b{display:block;font-weight:700;color:var(--text-dark);font-size:14.5px}

.footer{left:0;top:871px;width:1200px;height:129px;background:var(--footer);border-top:1px solid var(--rule)}
.footer-legal{left:120px;top:897px;font-size:12px;line-height:22px;color:var(--text)}
.footer-legal b{font-weight:700}
.footer-nav{left:764px;top:906px;font-size:12.5px;color:var(--green-bright);font-weight:600}
.footer-nav span{color:#999;margin:0 5px;font-weight:400}
.social{top:900px;width:30px;height:30px;background:var(--social);border-radius:2px}
</style>
</head>
<body>

<section class="hero abs">
  <div class="beans abs" role="img" aria-label="Pile of green coffee beans"></div>
  <div class="product-pack abs" role="img" aria-label="Lumen Vq green bean two bottle bonus pack box"></div>
  <p class="hero-copy abs">Lumen Vq Green Bean is made with premium green coffee bean that supplies 45% chlorogenic acid, which is the active weight-loss component of green coffee bean.</p>
  <a class="btn-learn abs">LEARN MORE<span>&#x276F;</span></a>
  <div class="tagline abs">Effective Weight Loss</div>
  <svg class="hero-notch abs" width="1200" height="24" viewBox="0 0 1200 24">
    <path d="M0 24 H515 C545 24 545 10 575 9 H625 C655 10 655 24 685 24 H1200 V24 H0Z" fill="#fff"/>
    <rect x="573" y="17" width="14" height="5" rx="2.5" fill="#5a9d17"/>
    <rect x="593" y="17" width="14" height="5" rx="2.5" fill="#dcdcdc"/>
    <rect x="613" y="17" width="14" height="5" rx="2.5" fill="#dcdcdc"/>
  </svg>
</section>

<h1 class="section-title abs">THE BEST OF NATURE &amp; SCIENCE</h1>
<p class="section-lead abs">New Lumen Vq is line of natural, high-quality, weight-loss supplements that are scientifically formulated for better efficiency!</p>

<section class="panel abs"></section>
<h2 class="panel-head abs">ALL OUR PRODUCTS ARE</h2>

<div class="photo-person abs" role="img" aria-label="Smiling woman with ponytail"></div>
<div class="photo-leaves abs" role="img" aria-label="Sprig of fresh green leaves"></div>

<div class="feature abs" style="top:522px">
  <svg width="26" height="28" viewBox="0 0 26 28"><path d="M2 26 C2 12 10 3 25 2 C24 16 16 25 2 26Z" fill="#7cc21e"/><path d="M3 25 L18 9" stroke="#fff" stroke-width="1.5"/></svg>
  <h3>100% PURE NATURAL INGREDIENTS</h3>
  <p>Lumen Vq products are made with 100% pure natural ingredients. Unlike other products, Lumen Vq products are made with premium natural ingredients for effective results.</p>
</div>
<div class="feature abs" style="top:632px">
  <svg width="26" height="28" viewBox="0 0 26 28"><path d="M2 26 C2 12 10 3 25 2 C24 16 16 25 2 26Z" fill="#7cc21e"/><path d="M3 25 L18 9" stroke="#fff" stroke-width="1.5"/></svg>
  <h3>SCIENTIFICALLY FORMULATED</h3>
  <p>Lumen Vq products are scientifically formulated to deliver the exact clinically tested doses that are needed to see results!</p>
</div>

<svg class="guarantee-seal abs" width="110" height="110" viewBox="0 0 110 110" role="img" aria-label="Guarantee seal">
  <circle cx="55" cy="55" r="53" fill="var(--gold)"/>
</svg>
<p class="guarantee-copy abs"><b>Lumen Vq is guaranteed to work or your money back.</b> Simply return it to the place of purchase within 30 days for a refund with original receipt.</p>

<svg class="trust-badge abs" width="70" height="72" viewBox="0 0 70 72" role="img" aria-label="Testing badge">
  <circle cx="35" cy="36" r="34" fill="var(--badge)"/>
</svg>
<p class="trust-copy abs">Lorem ipsum dolor sit amet, consectetur adipisicing elit, sed do eiusmod incididunt ut labore et dolore magna aliqua enim ad minim laboris nisi ut aliquip ext ... <a>Find out more</a></p>

<svg class="usa-shield abs" width="68" height="66" viewBox="0 0 68 66" role="img" aria-label="Manufacturing origin badge">
  <path d="M2 4 H66 V30 C66 48 50 60 34 65 C18 60 2 48 2 30Z" fill="#8d8a87"/>
</svg>
<p class="usa-copy abs"><b>Made in the USA</b>Lumen Vq is manufactured in a GMP-compliant manufacturing facility to ensure 100% quality.</p>

<footer class="footer abs"></footer>
<p class="footer-legal abs">© Copyright 2014 Ortel Works<br>Website by <b>Ortel Works</b></p>
<nav class="footer-nav abs">Home<span>|</span>Products<span>|</span>Contact Us</nav>
<a class="social abs" style="left:970px" aria-label="Social link"></a>
<a class="social abs" style="left:1010px" aria-label="Social link"></a>
<a class="social abs" style="left:1050px" aria-label="Social link"></a>

</body>
</html>
```